BUSINESS CARD DESIGN

NAME- DALE VORSKIN
PHONE NUMER - 555- 714-9082
EMAIL- OFFICE@TRV-GROUNDMAKRZ.COM
BACK OF CARD- SPEACIALIZES IN LAND CLEARING, FORESTRY MUCLHING AND EXCAVATION

Contact Information for Business Card

NAME- DALE VORSKIN PHONE NUMER - 555- 714-9082 EMAIL- OFFICE@TRV-GROUNDMAKRZ.COM BACK OF CARD- SPEACIALIZES IN LAND CLEARING , MUCLHING AND EXCAVATION

```html
<!DOCTYPE html>
<html lang="en">
<head>
<meta charset="UTF-8">
<title>Terravale Groundmakrz — Business Card</title>
<link rel="stylesheet" href="https://fonts.googleapis.com/css2?family=Montserrat:wght@400;500;700;800&display=swap">
<style>
  :root {
    --backdrop: #2e2e2e;
    --card-dark: #050505;
    --card-light: #ffffff;
    --gold: #f2ad1a;
    --ink: #151515;
    --ink-soft: #333333;
  }
  * { box-sizing: border-box; margin: 0; padding: 0; }
  html, body {
    width: 1200px; height: 1186px; overflow: hidden;
    background: var(--backdrop);
    font-family: "Montserrat", Arial, sans-serif;
  }
  .stage {
    width: 1200px; height: 1186px;
    display: flex; flex-direction: column; align-items: center; justify-content: center;
    gap: 60px;
  }
  .card {
    width: 880px; height: 503px; position: relative;
    box-shadow: 0 12px 30px rgba(0,0,0,.45);
  }
  /* Front */
  .card--front {
    background: var(--card-dark);
    display: flex; flex-direction: column; align-items: center; justify-content: center;
    color: var(--gold);
  }
  .brand-mark { width: 150px; height: 150px; border-radius: 50%; background: var(--gold); margin-bottom: 28px; }
  .brand-name {
    font-weight: 800; font-size: 40px; letter-spacing: 2px; text-align: center; line-height: 1.15;
  }
  .brand-sub { font-weight: 800; font-size: 22px; letter-spacing: 10px; margin-top: 8px; }
  .brand-rule { width: 380px; height: 3px; background: var(--gold); margin: 14px 0 10px; }
  .brand-phone { font-weight: 700; font-size: 22px; letter-spacing: 12px; }
  /* Back */
  .card--back { background: var(--card-light); color: var(--ink); }
  .back-brand {
    position: absolute; left: 70px; top: 60px; width: 360px;
    display: flex; flex-direction: column; align-items: center;
  }
  .back-brand .brand-mark { width: 80px; height: 80px; background: var(--ink); margin-bottom: 14px; }
  .back-brand .brand-name { font-size: 22px; color: var(--ink); }
  .back-brand .brand-sub { font-size: 12px; letter-spacing: 6px; color: var(--ink); margin-top: 4px; }
  .back-brand .brand-rule { width: 260px; height: 2px; background: var(--ink); margin: 8px 0 6px; }
  .back-brand .brand-phone { font-size: 13px; letter-spacing: 8px; color: var(--ink); }
  .person { position: absolute; left: 70px; top: 300px; }
  .person-name { color: var(--gold); font-weight: 700; font-size: 30px; letter-spacing: .5px; }
  .person-role { font-size: 17px; color: var(--ink-soft); margin: 4px 0 16px; }
  .contact-list { list-style: none; }
  .contact-item {
    display: flex; align-items: center; gap: 12px;
    font-size: 17px; color: var(--ink-soft); margin-bottom: 10px; letter-spacing: .3px;
  }
  .contact-item svg { width: 18px; height: 18px; flex: none; }
  .decor-mark {
    position: absolute; right: 70px; top: 70px;
    width: 330px; height: 330px; border-radius: 50%; background: var(--ink);
  }
</style>
</head>
<body>
<main class="stage">
  <section class="card card--front" aria-label="Card front">
    <div class="brand-mark" aria-hidden="true"></div>
    <div class="brand-name">TERRAVALE GROUNDMAKRZ</div>
    <div class="brand-sub">LLC · COASTAL</div>
    <div class="brand-rule"></div>
    <div class="brand-phone">555·714·9082</div>
  </section>

  <section class="card card--back" aria-label="Card back">
    <div class="back-brand">
      <div class="brand-mark" aria-hidden="true"></div>
      <div class="brand-name">TERRAVALE GROUNDMAKRZ</div>
      <div class="brand-sub">LLC · COASTAL</div>
      <div class="brand-rule"></div>
      <div class="brand-phone">555·714·9082</div>
    </div>

    <div class="person">
      <div class="person-name">DALE VORSKIN</div>
      <div class="person-role">Managing Director</div>
      <ul class="contact-list">
        <li class="contact-item">
          <svg viewBox="0 0 24 24" aria-hidden="true"><path fill="#f2ad1a" d="M6.6 10.8a15 15 0 0 0 6.6 6.6l2.2-2.2c.3-.3.7-.4 1-.2 1.1.4 2.3.6 3.6.6.6 0 1 .4 1 1V20c0 .6-.4 1-1 1A17 17 0 0 1 3 4c0-.6.4-1 1-1h3.5c.6 0 1 .4 1 1 0 1.3.2 2.5.6 3.6.1.3 0 .7-.2 1z"/></svg>
          555- 714-9082
        </li>
        <li class="contact-item">
          <svg viewBox="0 0 24 24" aria-hidden="true"><rect x="2" y="5" width="20" height="14" rx="2" fill="#f2ad1a"/><path d="M3 6l9 7 9-7" fill="none" stroke="#fff" stroke-width="1.6"/></svg>
          OFFICE@TRV-GROUNDMAKRZ.COM
        </li>
        <li class="contact-item">
          <svg viewBox="0 0 24 24" aria-hidden="true"><circle cx="12" cy="12" r="10" fill="#f2ad1a"/><path d="M2 12h20M12 2c3 3 3 17 0 20M12 2c-3 3-3 17 0 20" fill="none" stroke="#fff" stroke-width="1.4"/></svg>
          WWW.TRV-GROUNDMAKRZ.COM
        </li>
      </ul>
    </div>

    <div class="decor-mark" aria-hidden="true"></div>
  </section>
</main>
</body>
</html>
```